Business card design for holistic health care clinic

We need a double-sided business card design for our holistic health care clinic that integrates our logo design and also its color scheme. My business is called Valmira. It is an integrative medicine clinic. You have already done the logo for me. Please ensure an elegant and upscale design that is not cluttered, but still has all the necessary information (please see below for details).

Target Market(s)

Wellness, fitness, rehabilitation for educated, well-traveled open-minded clients who are focused on natural, organic, balanced and preventive healthcare and lifestyle.

Industry/Entity Type

Medical

Contact Information for Business Card

Modern, clean.

Number of Pages Required

1 page

Font styles to use
Serif
Sans Serif

Colors

Designer to choose colors to be used in the design.

Requirements
Must have
• Logo on one side, all other information on the other side.
• Other information should include:
• Tobias Wrenfeld - DOE, CPT, LMT
• 4100 East Marrow Drive
• Austin, TX 78119
• 512 555 0148
• 818 555 0192
• info@ValmiraHealth.example
• t.wrenfeld@ValmiraHealth.example
Nice to have
• Darker background on front - but not totally black - shaded/dark gray.

```html
<!DOCTYPE html>
<html lang="en">
<head>
<meta charset="utf-8">
<title>Valmira – Business Card</title>
<link href="https://fonts.googleapis.com/css2?family=Nunito:wght@600;800&family=Source+Sans+3:wght@400;600&display=swap" rel="stylesheet">
<style>
  :root {
    --backdrop: #454545;
    --card-light: #ececec;
    --card-dark: #222222;
    --brand-blue: #1a8fd1;
    --ink: #1c1c1c;
  }
  * { box-sizing: border-box; margin: 0; padding: 0; }
  html, body {
    width: 1200px;
    height: 900px;
    overflow: hidden;
    background: var(--backdrop);
  }
  .canvas {
    position: relative;
    width: 1200px;
    height: 900px;
  }
  .card {
    position: absolute;
    top: 170px;
    width: 347px;
    height: 561px;
    text-align: center;
  }
  .card--info { left: 259px; background: var(--card-light); }
  .card--brand { left: 631px; background: var(--card-dark); }

  .brand {
    position: absolute;
    left: 0;
    right: 0;
    color: var(--brand-blue);
    font-family: "Nunito", sans-serif;
  }
  .card--info .brand { top: 140px; }
  .card--brand .brand { top: 250px; }
  .brand__name {
    font-weight: 800;
    font-size: 56px;
    line-height: 1;
    letter-spacing: 1px;
  }
  .brand__tagline {
    margin-top: 8px;
    font-weight: 800;
    font-size: 16.5px;
    line-height: 1;
  }

  .contact {
    position: absolute;
    top: 346px;
    left: 0;
    right: 0;
    font-family: "Source Sans 3", sans-serif;
    color: var(--ink);
    font-size: 15.5px;
    line-height: 20px;
  }
  .contact__person {
    font-family: "Nunito", sans-serif;
    display: flex;
    justify-content: center;
    align-items: baseline;
    gap: 8px;
    padding-right: 8px;
  }
  .contact__name {
    color: var(--brand-blue);
    font-weight: 800;
    font-size: 19px;
  }
  .contact__credentials {
    font-family: "Source Sans 3", sans-serif;
    font-size: 15px;
  }
  .contact__rule {
    width: 171px;
    height: 1px;
    margin: 10px auto 12px 88px;
    background: var(--brand-blue);
  }
  .contact__address { margin-bottom: 12px; }
  .contact__label { color: var(--brand-blue); font-weight: 600; }

  .website {
    position: absolute;
    top: 497px;
    left: 0;
    right: 0;
    font-family: "Source Sans 3", sans-serif;
    font-size: 15.5px;
    color: var(--brand-blue);
  }
</style>
</head>
<body>
<main class="canvas">
  <section class="card card--info">
    <div class="brand">
      <div class="brand__name">VALMIRA</div>
      <div class="brand__tagline">Integrative Holistic Medicine</div>
    </div>
    <div class="contact">
      <div class="contact__person">
        <span class="contact__name">TOBIAS WRENFELD</span>
        <span class="contact__credentials">DOE, CPT, LMT</span>
      </div>
      <div class="contact__rule"></div>
      <p class="contact__address">4100 East Marrow Drive<br>Austin, TX 78119</p>
      <p><span class="contact__label">P:</span> 512 555 0148</p>
      <p><span class="contact__label">M:</span> 818 555 0192</p>
      <p><span class="contact__label">E:</span> info@ValmiraHealth.example</p>
      <p><span class="contact__label">E:</span> t.wrenfeld@ValmiraHealth.example</p>
    </div>
  </section>

  <section class="card card--brand">
    <div class="brand">
      <div class="brand__name">VALMIRA</div>
      <div class="brand__tagline">Integrative Holistic Medicine</div>
    </div>
    <p class="website">www.ValmiraHealth.example</p>
  </section>
</main>
</body>
</html>
```